Real Estate Company Looking for Business Card Designs for 3 Executives

Hello!
Thanks so much for considering our project! We are a real estate investment company located in Edmonton, Alberta called Bellhaven Group of Companies. We invest/develop both commercial and residential real estate and are looking to create 3 DOUBLE-SIDED business cards for 3 top executives in the company! (for some reason it won't let us select the double-sided option, but yes, the cards are double sided and would be happy to tip extra)

We have certain guidelines that we want our business cards to for sure follow - the back of the Business card has to be the Black Background Version of the Logo which has already been designed and linked as a file (first file). We want the entire back of the card to simply just be the black background logo. In terms of the front of the card, would like to see a smaller version of the white background logo (linked as the second file) in the top left hand corner - of course, feel free to get creative and we can make revisions together along the way! and Then after that, just text. We want the card to be sharp, clean, easy on the eyes and highly professional looking. We would like the card to include the Full name of the Company (Bellhaven Group of Companies), Name of the Person, Title, Phone, Email. If possible please provide the front part of the card for 3 people:

1) Bellhaven Group of Companies, Liora Quenby, Chief Financial Officer, 780-555-0142, lioraquenby@bellhavengroup.example

2) Bellhaven Group of Companies, Tobias Quenby, Chief Executive Officer, 780-555-0187, tobiasquenby@bellhavengroup.example

3) Bellhaven Group of Companies, Rui Delcourt, Chief Operations Officer, 587-555-0163, ruidelcourt@bellhavengroup.example

Thank you so much for considering our project & we look forward to seeing your designs!

```html
<!DOCTYPE html>
<html lang="en">
<head>
<meta charset="utf-8">
<title>Bellhaven Business Card</title>
<link rel="stylesheet" href="https://fonts.googleapis.com/css2?family=Poppins:wght@500;600&family=Arimo:wght@400&display=swap">
<style>
  :root {
    --backdrop: #b4b4b4;
    --ink: #050505;
    --paper: #ffffff;
    --shadow: rgba(0, 0, 0, 0.35);
  }
  * { box-sizing: border-box; margin: 0; padding: 0; }
  html, body {
    width: 1075px;
    height: 1200px;
    overflow: hidden;
    background: var(--backdrop);
  }
  .canvas {
    position: relative;
    width: 1075px;
    height: 1200px;
  }
  .card {
    position: absolute;
    left: 206px;
    width: 663px;
    height: 395px;
    box-shadow: 3px 3px 3px var(--shadow);
    overflow: hidden;
  }
  .card--front { top: 187px; background: var(--paper); }
  .card--back { top: 637px; background: var(--ink); }

  .front__band {
    position: absolute;
    left: 0; right: 0; bottom: 0;
    height: 135px;
    background: var(--ink);
  }
  .wordmark {
    position: absolute;
    font-family: "Poppins", sans-serif;
    font-weight: 500;
    letter-spacing: 7px;
    white-space: nowrap;
  }
  .card--front .wordmark {
    left: 380px;
    top: 125px;
    font-size: 27px;
    color: var(--ink);
  }
  .card--back .wordmark {
    left: 238px;
    top: 195px;
    font-size: 29px;
    color: var(--paper);
  }
  .person {
    position: absolute;
    left: 40px;
    top: 196px;
  }
  .person__name {
    font-family: "Poppins", sans-serif;
    font-weight: 600;
    font-size: 23px;
    line-height: 1.1;
    color: var(--ink);
    text-transform: uppercase;
  }
  .person__title {
    font-family: "Arimo", sans-serif;
    font-size: 16px;
    line-height: 1.3;
    color: var(--ink);
  }
  .contact {
    position: absolute;
    left: 40px;
    top: 316px;
    list-style: none;
    font-family: "Arimo", sans-serif;
    font-size: 16.5px;
    color: var(--paper);
  }
  .contact li {
    display: flex;
    align-items: center;
    gap: 5px;
    height: 22px;
  }
  .contact svg { width: 16px; height: 14px; fill: var(--paper); }
  .website {
    position: absolute;
    right: 45px;
    top: 337px;
    font-family: "Arimo", sans-serif;
    font-size: 16.5px;
    color: var(--paper);
  }
  .back__trees {
    position: absolute;
    left: 14px;
    top: 0;
    width: 178px;
    height: 395px;
    background: linear-gradient(180deg, #d9d9d9 0%, #8a8a8a 100%);
    opacity: 0.9;
  }
</style>
</head>
<body>
<div class="canvas">
  <section class="card card--front">
    <div class="wordmark">BELLHAVEN</div>
    <div class="person">
      <h1 class="person__name">Liora Quenby</h1>
      <p class="person__title">Chief Financial Officer</p>
    </div>
    <div class="front__band"></div>
    <ul class="contact">
      <li>
        <svg viewBox="0 0 24 24" aria-hidden="true"><path d="M6.6 10.8a15.1 15.1 0 0 0 6.6 6.6l2.2-2.2c.3-.3.7-.4 1-.2 1.1.4 2.3.6 3.6.6.6 0 1 .4 1 1V20c0 .6-.4 1-1 1C10.6 21 3 13.4 3 4c0-.6.4-1 1-1h3.5c.6 0 1 .4 1 1 0 1.3.2 2.5.6 3.6.1.3 0 .7-.2 1l-2.3 2.2z"/></svg>
        780-555-0142
      </li>
      <li>
        <svg viewBox="0 0 24 18" aria-hidden="true"><path d="M0 0h24v18H0z M2 2v1l10 7 10-7V2z" fill-rule="evenodd"/></svg>
        lioraquenby@bellhavengroup.example
      </li>
    </ul>
    <div class="website">www.bellhavengroup.example</div>
  </section>

  <section class="card card--back">
    <div class="back__trees" role="img" aria-label="White silhouettes of two tall pine trees rising from the bottom edge"></div>
    <div class="wordmark">BELLHAVEN</div>
  </section>
</div>
</body>
</html>
```